Postcard Design - Thanksgiving Card - Norvale Thermal Coils

Here are just a few of the heating and cooling products we offer:

• Steam Coils • Convector Coils
• Hot Water Coils • Re-Heat Coils
• Chilled Water Coils • Tube Bundles
• Direct Expansion (Evaporator) Coils • Shell & Tube Heat Exchangers
• Condensing Coils • Custom Coils to end user spec.’s

ENGINEERING - We can duplicate any existing equipment, even equipment that has been obsolete for years. Norvale Thermal personnel will come directly to your job site and match-up dimensions, materials, and performance - all free of charge. We can build from copper, aluminum, cupro-nickel, brass, and more. Heat exchangers and tube bundles can be replaced & warranted as new with great savings; this includes Hadley & Prowse, Wexford-Lanning, Zuno, and others. We also make engineering recommendations and suggestions regarding the correct ways to replace equipment or methods of increasing the life expectancy of equipment. We will help solve your HVAC problems, not duplicate them.

Hvac

```html
<!DOCTYPE html>
<html lang="en">
<head>
<meta charset="utf-8">
<title>Norvale Thermal Coils – Thanksgiving Postcard</title>
<link href="https://fonts.googleapis.com/css2?family=Lato:ital,wght@1,300&family=Montserrat:wght@400;600;700&family=Great+Vibes&display=swap" rel="stylesheet">
<style>
  :root {
    --stage: #000000;
    --paper: #ffffff;
    --brown: #5a2418;
    --brown-band: #6a2e20;
    --ink: #1e1e1e;
    --quote: #4a4a4a;
    --copper-dark: #6e3a22;
    --copper: #b06a45;
    --steel: #cfcfd2;
    --leaf: #e9c7a8;
    --leaf-soft: #f6e6dc;
  }
  * { margin: 0; padding: 0; box-sizing: border-box; }
  html, body { width: 784px; height: 1200px; overflow: hidden; background: var(--stage); }
  .canvas { position: relative; width: 784px; height: 1200px; background: var(--stage); }

  .postcard { position: absolute; left: 88px; width: 611px; height: 473px; background: var(--paper); overflow: hidden; }
  .postcard--front { top: 91px; }
  .postcard--back { top: 618px; }

  /* Front */
  .coil-photo {
    position: absolute; left: 0; top: 0; width: 611px; height: 330px;
    background:
      linear-gradient(180deg, rgba(255,255,255,0) 55%, #ffffff 100%),
      linear-gradient(160deg, var(--copper-dark) 0%, var(--copper) 35%, var(--steel) 62%, #f2f2f2 80%);
  }
  .quote {
    position: absolute; left: 270px; top: 208px; width: 330px;
    font-family: "Lato", sans-serif; font-style: italic; font-weight: 300;
    font-size: 14.6px; line-height: 22.6px; color: var(--quote); text-align: center;
    letter-spacing: -0.3px;
  }
  .signature {
    position: absolute; left: 370px; top: 323px; width: 126px; height: 30px;
    background: var(--brown); opacity: 0.18; border-radius: 4px;
  }
  .brand { position: absolute; text-align: center; font-family: "Montserrat", sans-serif; color: var(--ink); }
  .brand__name { font-weight: 700; font-size: 16px; letter-spacing: 0.5px; }
  .brand__tag { font-weight: 600; font-size: 9.5px; letter-spacing: 0.3px; margin-top: 4px; }
  .postcard--front .brand { left: 34px; top: 290px; width: 200px; }
  .brand__mark { display: inline-block; width: 14px; height: 14px; background: var(--brown); margin-right: 6px; vertical-align: -1px; }

  .contact-line {
    position: absolute; left: 0; top: 380px; width: 611px; text-align: center;
    font-family: "Montserrat", sans-serif; font-size: 13px; color: var(--ink); padding-left: 100px;
  }
  .contact-line strong { font-weight: 700; }
  .rule { position: absolute; left: 0; top: 404px; width: 611px; height: 1.5px; background: var(--brown); }
  .products {
    position: absolute; left: 0; top: 412px; width: 611px; text-align: center;
    font-family: "Montserrat", sans-serif; font-size: 11.4px; line-height: 14.8px; color: var(--ink);
  }

  /* Back */
  .leaf-photo {
    position: absolute; inset: 0;
    background:
      radial-gradient(ellipse 70% 80% at 80% 45%, #ffffff 0%, rgba(255,255,255,0.9) 35%, rgba(255,255,255,0) 75%),
      linear-gradient(135deg, var(--leaf) 0%, var(--leaf-soft) 45%, #f4e8e4 70%, #f3e2d0 100%);
  }
  .leaf-ornament {
    position: absolute; left: 130px; top: 54px; width: 80px; height: 56px;
    background: #c79a6a; opacity: 0.55; border-radius: 50% 50% 50% 10%;
  }
  .greeting {
    position: absolute; left: 40px; top: 108px; width: 280px;
    font-family: "Great Vibes", cursive; color: var(--brown); font-size: 50px; line-height: 46px;
  }
  .greeting span { display: block; }
  .greeting .greeting__first { padding-left: 48px; }
  .postcard--back .brand { left: 64px; top: 262px; width: 180px; }
  .back-contact { position: absolute; left: 73px; top: 337px; width: 184px; text-align: center; font-family: "Montserrat", sans-serif; color: var(--ink); }
  .back-contact__band { background: var(--brown-band); color: #fff; font-weight: 600; font-size: 12.5px; line-height: 19px; }
  .back-contact__phone { font-weight: 700; font-size: 19px; line-height: 22px; margin-top: 2px; }
  .back-contact__line { font-size: 12.5px; line-height: 15.5px; }
</style>
</head>
<body>
<div class="canvas">

  <section class="postcard postcard--front">
    <div class="coil-photo" role="img" aria-label="Close-up photograph of copper return bends on a heat exchanger coil header"></div>
    <p class="quote">“It is the time of Year for remembering everything that makes us grateful. That is why we want to express our appreciation for your confidence in our firm to assist you on your jobsite or at your facility to solve a coil or heat exchanger problem.”</p>
    <div class="signature" role="img" aria-label="Handwritten signature"></div>
    <div class="brand">
      <div class="brand__name"><span class="brand__mark"></span>Norvale Thermal Coils</div>
      <div class="brand__tag">HVACR COILS • HEAT EXCHANGERS</div>
    </div>
    <p class="contact-line">Harlow &amp; Brennick &nbsp;|&nbsp; <strong>888-555-0142</strong> &nbsp;|&nbsp; coilguy@norvalemail.net</p>
    <div class="rule"></div>
    <p class="products">
      • Steam Coils • Hot Water Coils • Chilled Water Coils • Condensing Coils<br>
      • Direct Expansion (Evaporator) Coils • Convector Coils • Re-Heat Coils • Tube Bundles<br>
      • Shell &amp; Tube Heat Exchangers • Custom Coils to end user spec.’s
    </p>
  </section>

  <section class="postcard postcard--back">
    <div class="leaf-photo" role="img" aria-label="Soft-focus photograph of a pale autumn maple leaf"></div>
    <div class="leaf-ornament" role="img" aria-label="Small autumn leaves ornament"></div>
    <h1 class="greeting"><span class="greeting__first">Happy</span><span>Thanksgiving!</span></h1>
    <div class="brand">
      <div class="brand__name"><span class="brand__mark"></span>Norvale Thermal Coils</div>
      <div class="brand__tag">HVACR COILS • HEAT EXCHANGERS</div>
    </div>
    <div class="back-contact">
      <div class="back-contact__band">Harlow &amp; Brennick</div>
      <div class="back-contact__phone">888-555-0142</div>
      <div class="back-contact__line">coilguy@norvalemail.net</div>
      <div class="back-contact__line">Dale Orrin &amp; Russ Pellam</div>
      <div class="back-contact__line">P.O. Box 718</div>
      <div class="back-contact__line">Brennick, MI 48090</div>
    </div>
  </section>

</div>
</body>
</html>
```